Amber Vital 480

This is a 9 week program we conduct in our gym/recovery facility with the aim of educating members on the ins and outs of training, sauna use, cold plunge, sleep and lifestyle factors that they need to consider to increase health span into their older age. It is geared towards the Gen X age group.

```html
<!DOCTYPE html>
<html lang="en">
<head>
<meta charset="UTF-8">
<title>Amber Vital 480 – 9-Week Program</title>
<link href="https://fonts.googleapis.com/css2?family=Kanit:wght@300;400;500;600&display=swap" rel="stylesheet">
<style>
:root{
  --blue:#1a82c9;
  --blue-bright:#2a8fd6;
  --ink:#1c1c1c;
  --muted:#5a5a5a;
  --black:#000;
  --white:#fff;
  --line:#3a3a3a;
}
*{margin:0;padding:0;box-sizing:border-box}
html,body{width:1200px;height:3748px;overflow:hidden}
body{font-family:"Kanit",sans-serif;color:var(--ink);background:var(--white);position:relative}
.abs{position:absolute}
.btn{position:absolute;display:flex;align-items:center;justify-content:center;border-radius:24px;background:var(--blue-bright);color:var(--white);font-size:19px;font-weight:400}

/* header */
.site-header{position:absolute;left:0;top:0;width:1200px;height:106px;background:linear-gradient(90deg,#e4f0fa 0%,#fff 35%,#fff 100%)}
.brand{position:absolute;left:102px;top:18px;display:flex;align-items:center;gap:14px}
.brand-dot{width:70px;height:70px;border-radius:50%;border:4px solid var(--blue)}
.brand-name{font-size:27px;font-weight:500;line-height:1.15;color:var(--ink);width:170px}
.contact{position:absolute;top:28px;display:flex;align-items:center;gap:12px;font-size:14px;font-weight:300;color:#777}
.contact-icon{width:42px;height:42px;border-radius:50%;background:var(--blue);display:flex;align-items:center;justify-content:center}
.menu{position:absolute;left:1020px;top:36px;display:flex;align-items:center;gap:9px;font-size:16px;font-weight:300;color:#666}

/* hero */
.hero{position:absolute;left:0;top:106px;width:1200px;height:515px}
.hero-photo{position:absolute;inset:0;background:linear-gradient(100deg,#8fb8d8 0%,#6d9c75 30%,#9cb37a 55%,#c9c6b4 75%,#7fa266 100%)}
.hero-fade{position:absolute;left:0;top:0;width:560px;height:515px;background:radial-gradient(ellipse at 35% 50%,rgba(90,150,205,.55),rgba(90,150,205,0) 70%)}
.hero-title{position:absolute;left:123px;top:150px;font-size:46px;font-weight:400;color:var(--white)}
.hero-title b{font-weight:600}
.hero-text{position:absolute;left:114px;top:224px;width:380px;font-size:14px;font-weight:300;line-height:23px;color:var(--white)}
.hero-btn{position:absolute;left:114px;top:318px;width:152px;height:44px;border-radius:22px;background:var(--black);color:var(--white);font-size:19px;font-weight:500;display:flex;align-items:center;justify-content:center}
.hero-arrow{position:absolute;top:240px}

/* about */
.about{position:absolute;left:0;top:621px;width:1200px;height:447px;text-align:center}
.eyebrow{font-size:28px;font-weight:300}
.heading{font-size:37px;font-weight:500;color:var(--blue)}
.about .eyebrow{position:absolute;left:0;width:1200px;top:76px}
.about .heading{position:absolute;left:0;width:1200px;top:110px}
.about-text{position:absolute;left:150px;top:172px;width:900px;font-size:14px;font-weight:300;line-height:26px;color:var(--muted)}

/* program */
.program{position:absolute;left:0;top:1068px;width:1200px;height:1752px;background:var(--black);color:var(--white)}
.program .eyebrow{position:absolute;left:0;width:1200px;top:52px;text-align:center}
.program .heading{position:absolute;left:0;width:1200px;top:88px;text-align:center;font-size:38px}
.week{position:absolute;width:323px}
.week-photo{width:323px;height:239px}
.week-bar{position:absolute;left:29px;top:180px;width:3px;height:150px;background:var(--blue)}
.week-title{position:absolute;left:52px;top:258px;font-size:24px;font-weight:400}
.week-text{position:absolute;left:55px;top:300px;width:260px;font-size:16px;font-weight:400;line-height:26px}
.divider{position:absolute;left:99px;top:1141px;width:1001px;height:1px;background:var(--line)}
.wwd-eyebrow{position:absolute;left:117px;top:1190px;font-size:28px;font-weight:300}
.wwd-heading{position:absolute;left:116px;top:1226px;font-size:46px;font-weight:500}
.wwd-heading span{color:var(--blue)}
.wwd-text{position:absolute;left:117px;top:1300px;width:510px;font-size:14px;font-weight:300;line-height:26px}

/* why */
.why{position:absolute;left:0;top:2820px;width:1200px;height:508px;text-align:center}
.why .eyebrow{position:absolute;left:0;width:1200px;top:82px}
.why .heading{position:absolute;left:0;width:1200px;top:120px}
.feature{position:absolute;width:220px;text-align:center}
.feature-label{font-size:19px;font-weight:500;margin-top:4px}

/* footer */
.site-footer{position:absolute;left:0;top:3328px;width:1200px;height:420px;background:var(--blue);color:var(--white)}
.footer-brand{position:absolute;left:410px;top:66px;display:flex;align-items:center;gap:22px}
.footer-dot{width:110px;height:110px;border-radius:50%;border:5px solid var(--white)}
.footer-name{font-size:44px;font-weight:500;line-height:1.1;width:260px}
.socials{position:absolute;left:481px;top:232px;display:flex;gap:13px}
.social{width:50px;height:50px;border-radius:50%;border:3px solid var(--white);background:rgba(255,255,255,.1)}
.copyright{position:absolute;left:0;width:1200px;top:348px;text-align:center;font-size:19px;font-weight:300}
</style>
</head>
<body>

<header class="site-header">
  <div class="brand"><div class="brand-dot"></div><div class="brand-name">Amber Vital 480</div></div>
  <div class="contact" style="left:514px">
    <div class="contact-icon"><svg width="22" height="16" viewBox="0 0 22 16"><rect x="1" y="1" width="20" height="14" fill="none" stroke="#fff" stroke-width="2"/><path d="M1 1l10 8 10-8" fill="none" stroke="#fff" stroke-width="2"/></svg></div>
    info@ambervital480.com
  </div>
  <div class="contact" style="left:768px">
    <div class="contact-icon"><svg width="20" height="20" viewBox="0 0 24 24"><path d="M6.6 10.8a15 15 0 006.6 6.6l2.2-2.2a1 1 0 011-.25 11.4 11.4 0 003.6.6 1 1 0 011 1V20a1 1 0 01-1 1A17 17 0 013 4a1 1 0 011-1h3.5a1 1 0 011 1c0 1.25.2 2.45.6 3.6a1 1 0 01-.25 1z" fill="#fff"/></svg></div>
    +1 555-010-4800
  </div>
  <div class="menu">Menu <svg width="28" height="18" viewBox="0 0 28 18"><path d="M0 2h28M0 9h28M0 16h28" stroke="#333" stroke-width="2.4"/></svg></div>
</header>

<section class="hero">
  <div class="hero-photo" role="img" aria-label="Photo of a smiling older couple embracing outdoors among green trees"></div>
  <div class="hero-fade"></div>
  <h1 class="hero-title"><b>Amber</b> Vital <b>480</b></h1>
  <p class="hero-text">Lorem ipsum dolor sit amet, consectetur adipiscing elit, sed do eiusmod tempor incididunt ut labore et dolore magna aliqua.</p>
  <div class="hero-btn">Get Started</div>
  <svg class="hero-arrow" style="left:44px" width="16" height="30" viewBox="0 0 16 30"><path d="M14 2L2 15l12 13" fill="none" stroke="#4a6a80" stroke-width="2.5"/></svg>
  <svg class="hero-arrow" style="left:1146px" width="16" height="30" viewBox="0 0 16 30"><path d="M2 2l12 13L2 28" fill="none" stroke="#eee" stroke-width="2.5"/></svg>
</section>

<section class="about">
  <p class="eyebrow">About Us</p>
  <h2 class="heading">Our Gym/Recovery Facility</h2>
  <p class="about-text">Sed ut perspiciatis unde omnis iste natus error sit voluptatem accusantium doloremque laudantium, totam rem aperiam, eaque ipsa quae ab illo inventore veritatis et quasi architecto beatae vitae dicta sunt explicabo. Nemo enim ipsam voluptatem quia voluptas sit aspernatur aut odit aut fugit, sed quia consequuntur magni dolores eos qui ratione voluptatem sequi nesciunt. Neque porro quisquam est, qui dolorem ipsum quia dolor sit amet, consectetur, adipisci velit, sed quia non numquam eius modi tempora incidunt ut labore et dolore magnam aliquam quaerat voluptatem.</p>
  <div class="btn" style="left:533px;top:322px;width:134px;height:44px">Join Now</div>
</section>

<section class="program">
  <p class="eyebrow">Program</p>
  <h2 class="heading">9-Week Program</h2>

  <article class="week" style="left:103px;top:174px">
    <div class="week-photo" role="img" aria-label="Photo of a trainer helping an older woman exercise" style="background:linear-gradient(135deg,#e8eef0,#b9c6cf 60%,#3b6fa8)"></div>
    <div class="week-bar"></div><h3 class="week-title">1 Week</h3>
    <p class="week-text">Lorem ipsum dolor sit amet, consectetur adipiscing elit, sed do eiusmod tempor</p>
  </article>
  <article class="week" style="left:442px;top:174px">
    <div class="week-photo" role="img" aria-label="Photo of an older couple jogging outdoors at sunset" style="background:linear-gradient(135deg,#5b5a3a,#a5833f 50%,#d9a64f)"></div>
    <div class="week-bar"></div><h3 class="week-title">2 Week</h3>
    <p class="week-text">Lorem ipsum dolor sit amet, consectetur adipiscing elit, sed do eiusmod tempor</p>
  </article>
  <article class="week" style="left:781px;top:174px">
    <div class="week-photo" role="img" aria-label="Photo of a woman relaxing in a wooden sauna" style="background:linear-gradient(135deg,#4d3a2c,#8a6a50 50%,#c9b8a6)"></div>
    <div class="week-bar"></div><h3 class="week-title">3 Week</h3>
    <p class="week-text">Lorem ipsum dolor sit amet, consectetur adipiscing elit, sed do eiusmod tempor</p>
  </article>

  <article class="week" style="left:103px;top:599px">
    <div class="week-photo" role="img" aria-label="Photo of an older couple in ice baths" style="background:linear-gradient(135deg,#1f3d73,#5a82b8 50%,#c9d8ea)"></div>
    <div class="week-bar"></div><h3 class="week-title">4 Week</h3>
    <p class="week-text">Lorem ipsum dolor sit amet, consectetur adipiscing elit, sed do eiusmod tempor</p>
  </article>
  <article class="week" style="left:442px;top:599px">
    <div class="week-photo" role="img" aria-label="Photo of an older couple sleeping in bed" style="background:linear-gradient(135deg,#e6ddd0,#c9b7a2 50%,#a68f7a)"></div>
    <div class="week-bar"></div><h3 class="week-title">5 Week</h3>
    <p class="week-text">Lorem ipsum dolor sit amet, consectetur adipiscing elit, sed do eiusmod tempor</p>
  </article>
  <article class="week" style="left:781px;top:599px">
    <div class="week-photo" role="img" aria-label="Photo of an older woman sleeping on white pillows" style="background:linear-gradient(135deg,#f2f3f6,#d7dbe4 60%,#aeb7c8)"></div>
    <div class="week-bar"></div><h3 class="week-title">6 Week</h3>
    <p class="week-text">Lorem ipsum dolor sit amet, consectetur adipiscing elit, sed do eiusmod tempor</p>
  </article>

  <div class="btn" style="left:522px;top:1029px;width:156px;height:44px">Load More</div>

  <div class="divider"></div>
  <p class="wwd-eyebrow">What we do</p>
  <h2 class="wwd-heading">About <span>Us</span></h2>
  <p class="wwd-text">Sed ut perspiciatis unde omnis iste natus error sit voluptatem accusantium doloremque laudantium, totam rem aperiam, eaque ipsa quae ab illo inventore veritatis et quasi architecto beatae vitae dicta sunt explicabo. Nemo enim ipsam voluptatem quia voluptas sit aspernatur aut odit aut fugit, sed quia consequuntur magni dolores eos qui ratione voluptatem sequi nesciunt. Neque porro quisquam est, qui dolorem ipsum quia dolor sit amet, consectetur, adipisci velit, sed quia non numquam eius modi tempora incidunt ut labore et dolore magnam aliquam quaerat voluptatem.</p>
  <div class="btn" style="left:114px;top:1552px;width:156px;height:44px">Load More</div>

  <svg class="abs" style="left:675px;top:1200px" width="460" height="446" viewBox="0 0 460 446">
    <polygon points="458,2 458,444 12,444 40,416 420,416 420,40" fill="#1a82c9"/>
    <rect x="1" y="1" width="405" height="396" fill="none" stroke="#1a82c9" stroke-width="2"/>
  </svg>
  <div class="abs" role="img" aria-label="Photo of older adults doing lunges on grass in a park" style="left:689px;top:1213px;width:406px;height:397px;background:linear-gradient(160deg,#c9d6b9,#93ae6c 45%,#5f8a3a)"></div>
</section>

<section class="why">
  <p class="eyebrow">Why Choose Us</p>
  <h2 class="heading">Amber Vital 480</h2>
  <svg class="abs" style="left:0;top:0" width="1200" height="508"><path d="M282 306L420 334M532 334L670 306M782 306L920 334" stroke="#bbb" stroke-width="1.5" stroke-dasharray="5 4" fill="none"/></svg>

  <div class="feature" style="left:115px;top:205px">
    <svg width="116" height="116" viewBox="0 0 116 116"><polygon points="58,3 106,30 106,86 58,113 10,86 10,30" fill="#1a82c9" stroke="#000" stroke-width="4"/><rect x="38" y="38" width="40" height="34" fill="none" stroke="#fff" stroke-width="2.5"/><path d="M44 64l8-10 8 6 10-14" stroke="#fff" stroke-width="2.5" fill="none"/></svg>
    <p class="feature-label">Training</p>
  </div>
  <div class="feature" style="left:366px;top:248px">
    <svg width="116" height="116" viewBox="0 0 116 116"><polygon points="58,3 106,30 106,86 58,113 10,86 10,30" fill="#1a82c9" stroke="#000" stroke-width="4"/><path d="M38 52h40l-5 30H43z" fill="none" stroke="#fff" stroke-width="2.5"/><path d="M46 52v-10h14" stroke="#fff" stroke-width="2.5" fill="none"/></svg>
    <p class="feature-label">Sauna Use</p>
  </div>
  <div class="feature" style="left:616px;top:205px">
    <svg width="116" height="116" viewBox="0 0 116 116"><polygon points="58,3 106,30 106,86 58,113 10,86 10,30" fill="#1a82c9" stroke="#000" stroke-width="4"/><rect x="44" y="44" width="28" height="40" rx="5" fill="none" stroke="#fff" stroke-width="2.5"/><rect x="50" y="34" width="16" height="10" fill="none" stroke="#fff" stroke-width="2.5"/></svg>
    <p class="feature-label">Cold Plunge</p>
  </div>
  <div class="feature" style="left:866px;top:248px">
    <svg width="116" height="116" viewBox="0 0 116 116"><polygon points="58,3 106,30 106,86 58,113 10,86 10,30" fill="#1a82c9" stroke="#000" stroke-width="4"/><path d="M34 76V48M34 66h48v10M40 58h14" stroke="#fff" stroke-width="2.5" fill="none"/><circle cx="72" cy="56" r="8" fill="none" stroke="#fff" stroke-width="2.5"/></svg>
    <p class="feature-label">Sleep and Lifestyle</p>
  </div>
</section>

<footer class="site-footer">
  <div class="footer-brand"><div class="footer-dot"></div><div class="footer-name">Amber Vital 480</div></div>
  <div class="socials">
    <div class="social" role="img" aria-label="Social network link"></div>
    <div class="social" role="img" aria-label="Social network link"></div>
    <div class="social" role="img" aria-label="Social network link"></div>
    <div class="social" role="img" aria-label="Social network link"></div>
  </div>
  <p class="copyright">© 2024 Amber Vital 480&nbsp; All Rights Reserved</p>
</footer>

</body>
</html>
```